Web and Logo Design for eCommerce site

We're launching a sister brand and require a full design for the site.

The site must have an established feel and appeal to corporate and institutional buyers.
Updates

Just a note about the wireframe design:

The Search & Rescue / Coast Guard / NVDK, etc. in the header area aren't buttons or menu items, but rather just info (along the lines of a tagline).  Sort of a "who we serve" sort of thing.

Worth noting is that it's specifically geared towards LARGE BUYERS.  For example, a police force buying 200 headlamps and 85 pairs of gloves.  So they'll register + sign in and then add a bunch of items to a RFQ.

Aim for a professional, masculine design.

Target Market(s)

We will be selling outdoor gear to the military, law enforcement, fire and rescue and first responders.

Requirements
Must have
• We require:
- Logo (vector based)

Site:
- template page
* main site template, re-skinned version of our current site
* horizontal drop-down menu
- product listings page
* thumbnail view of products
- product details page
* including elements such as product image, color/size selector, descriptions and specs (again, based loosely on our current website)
- account management page
* illustrating basic data entry styles for text box, buttons, grid, etc.

The site needs to be given a responsive design, so 2 versions of each design should be presented for desktop + mobile views.

Additional funds are available if the designer is able to fully implement the designs into a responsive framework such as bootstrap.

Nice to have
• Clean, professional design similar to:

http://military.trailvexagear.com/gov/accessories/gloves.html

http://leaf.ombrivo.com/ProductFind.aspx?language=EN&category=Hardshell&subcat=Waterproof_Jackets

```html
<!DOCTYPE html>
<html lang="en">
<head>
<meta charset="utf-8">
<title>NordKit — Canada Outdoor Pro Supply</title>
<link href="https://fonts.googleapis.com/css2?family=Roboto:wght@300;400;500&display=swap" rel="stylesheet">
<style>
:root{
  --header:#1c1c1c;
  --strip:#e6e6e6;
  --blue:#2f8fca;
  --blue-text:#2a8fc9;
  --page:#f1f1f1;
  --card:#fbfbfb;
  --line:#d9d9d9;
  --muted:#7d7d7d;
  --footer:#262626;
  --footer-base:#1b1b1b;
  --veil:rgba(38,38,38,.58);
  --button-dark:#2f2f2f;
}
*{box-sizing:border-box;margin:0;padding:0}
html,body{width:838px;height:1200px;overflow:hidden}
body{font-family:"Roboto",Arial,sans-serif;background:var(--page);position:relative;color:var(--muted)}
.abs{position:absolute}
.site-header{left:0;top:0;width:838px;height:63px;background:var(--header)}
.brand{left:91px;top:10px;color:var(--blue);font-size:26px;font-weight:400;letter-spacing:.5px}
.brand-sub{left:91px;top:41px;font-size:8px;color:var(--blue)}
.login{left:372px;top:22px;display:flex;align-items:center;gap:6px;font-size:9px;color:#bfbfbf}
.login-icon{width:20px;height:20px;background:var(--blue);display:flex;align-items:center;justify-content:center}
.header-quote{right:92px;top:16px;text-align:right;font-size:10.5px;line-height:16px;color:#d0d0d0}
.serve-strip{left:0;top:63px;width:838px;height:37px;background:var(--strip);border-bottom:1px solid #ccc}
.serve-list{left:92px;top:63px;height:37px;display:flex;align-items:center;font-size:10.5px;color:#555}
.serve-list span{padding:0 14px;border-right:1px solid #cfcfcf}
.serve-list span:last-child{border-right:0}
.search-box{left:624px;top:70px;width:78px;height:23px;background:#fff;border:1px solid #ccc}
.search-btn{left:702px;top:70px;width:45px;height:23px;background:var(--blue);color:#fff;font-size:9px;display:flex;align-items:center;justify-content:center}
.main-nav{left:0;top:100px;width:838px;height:36px;background:var(--blue)}
.main-nav span{position:absolute;top:12px;font-size:10.5px;color:#eaf4fb}
.hero{left:0;top:136px;width:838px;height:314px;background:linear-gradient(135deg,#f2f4f6 0%,#cfd6dc 45%,#eef1f3 70%,#b9c2c9 100%)}
.categories{left:94px;top:473px;width:152px;height:230px;background:#fff;border:1px solid var(--line)}
.cat-head{height:20px;background:var(--blue);color:#fff;font-size:12px;padding:3px 6px;font-weight:300}
.cat-item{height:23px;margin:0 10px 0 6px;border-bottom:1px solid #eee;font-size:8px;line-height:22px;display:flex;justify-content:space-between;white-space:nowrap;overflow:hidden}
.promo{left:92px;top:725px;width:153px;height:115px;background:linear-gradient(160deg,#5b5048,#2d2a27)}
.sort-bar{left:598px;top:470px;width:148px;height:23px;background:#fff;border:1px solid var(--line);font-size:9px;line-height:21px;padding-left:6px}
.sort-bar b{font-weight:400;color:#333}
.card{width:151px;height:156px;background:var(--card);border:1px solid #ececec;text-align:center}
.card .flag{position:absolute;left:0;top:0;width:0;height:0;border-top:24px solid var(--blue);border-right:24px solid transparent}
.card .thumb{position:absolute;left:58px;top:20px;width:36px;height:60px;border-radius:6px}
.card .name{position:absolute;left:0;right:0;top:118px;font-size:8.5px;color:#666}
.card .price{position:absolute;left:0;right:0;top:132px;font-size:9.5px;color:var(--blue)}
.pager{left:414px;top:862px;display:flex;gap:3.3px}
.pager span{width:14px;height:14px;border-radius:50%;background:#e2e2e2;font-size:7px;line-height:14px;text-align:center;color:#444}
.pager .on{background:var(--blue);color:#fff}
.testimonials{left:0;top:898px;width:838px;height:46px;background:var(--blue)}
.t-label{left:90px;top:910px;width:70px;height:22px;border:1px solid rgba(255,255,255,.35);color:#fff;font-size:9.5px;line-height:20px;text-align:center}
.t-text{left:210px;top:908px;width:430px;font-size:8.5px;line-height:12px;color:#eaf4fb}
.t-arrow{left:710px;top:906px;width:32px;height:32px;border:1px solid rgba(255,255,255,.35)}
.footer{left:0;top:944px;width:838px;height:193px;background:var(--footer)}
.f-col{top:968px}
.f-col h3{font-size:14px;font-weight:300;color:#ddd;margin-bottom:9px}
.f-col li{list-style:none;font-size:7.5px;color:#9a9a9a;height:16.4px;padding-left:12px;position:relative}
.f-col li:before{content:"›";position:absolute;left:1px;top:-3px;font-size:11px;color:#ccc}
.f-col p{font-size:7.5px;line-height:15px;color:#9a9a9a;width:140px}
.f-input{width:133px;height:17px;background:#fff;margin-top:8px;font-size:7px;color:#aaa;padding:4px 6px}
.f-btn{margin-top:12px;width:56px;height:16px;background:var(--blue);color:#fff;font-size:9.5px;text-align:center;line-height:16px}
.base{left:0;top:1137px;width:838px;height:63px;background:var(--footer-base)}
.copyright{left:95px;top:1165px;font-size:7.5px;color:#8a8a8a}
.social{top:1156px;width:28px;height:28px;border-radius:50%;background:#bdbdbd}
.veil{left:0;top:0;width:838px;height:1200px;background:var(--veil)}
.modal{left:204px;top:355px;width:400px;height:209px;background:linear-gradient(#fafafa,#e4e4e4);text-align:center}
.modal-copy{margin-top:23px;font-size:12.2px;line-height:23px;color:var(--blue-text);text-transform:uppercase}
.modal-btn{display:inline-block;margin-top:15px;width:126px;height:28px;background:var(--button-dark);color:#fff;font-size:14px;line-height:28px;border:1px solid #555}
.close{left:593px;top:550px;width:24px;height:24px;border-radius:50%;background:#000;border:2px solid #fff;color:#fff;font-size:11px;line-height:20px;text-align:center}
</style>
</head>
<body>
<header>
  <div class="abs site-header"></div>
  <div class="abs brand">NordKit</div>
  <div class="abs brand-sub">Canada Outdoor Pro Supply</div>
  <div class="abs login">
    <span class="login-icon"><svg width="10" height="11" viewBox="0 0 10 11"><rect x="1" y="5" width="8" height="6" fill="#fff"/><path d="M3 5V3a2 2 0 0 1 4 0v2" stroke="#fff" fill="none" stroke-width="1.3"/></svg></span>
    Customer Login
  </div>
  <div class="abs header-quote">“ Great Outdoor Gear For<br>Canada's First Responders”</div>
  <div class="abs serve-strip"></div>
  <div class="abs serve-list"><span>Search &amp; Rescue</span><span>Coast Guard</span><span>NVDK</span><span>Fire</span><span>Military</span><span>Law Enforcement</span></div>
  <div class="abs search-box"><svg width="14" height="14" viewBox="0 0 14 14" style="margin:4px"><circle cx="5.5" cy="5.5" r="4" stroke="#999" fill="none" stroke-width="1.4"/><path d="M8.5 8.5l4 4" stroke="#999" stroke-width="1.6"/></svg></div>
  <div class="abs search-btn">Search</div>
  <nav class="abs main-nav">
    <span style="left:91px">Resucue Gear</span><span style="left:194px">Footwear</span><span style="left:276px">Clothing</span><span style="left:350px">Tents, Mats, Sleeping Bags</span><span style="left:512px">Camping Gear</span><span style="left:616px">Snow Sports</span><span style="left:714px">Brands</span>
  </nav>
</header>

<div class="abs hero" role="img" aria-label="Mountaineer in a yellow jacket climbing a snowy ridge"></div>

<aside class="abs categories">
  <div class="cat-head">Categories</div>
  <div class="cat-item">Quisque semper justo at risus</div>
  <div class="cat-item">Amet lectus quis est congue</div>
  <div class="cat-item">Proin nibh augue</div>
  <div class="cat-item"><span>Quisque semper justo at risus</span><span>›</span></div>
  <div class="cat-item">Amet lectus quis est congue</div>
  <div class="cat-item"><span>Proin nibh augue</span><span>›</span></div>
  <div class="cat-item"><span>Etiam sit amet lectus quis</span><span>›</span></div>
  <div class="cat-item">Proin nibh augue</div>
  <div class="cat-item" style="border:0">Etiam sit amet lectus quis</div>
</aside>
<div class="abs promo" role="img" aria-label="Member pass promotion banner with an adventurer photo"></div>

<div class="abs sort-bar">By: <b>Defult ▾</b> &nbsp;/&nbsp; Price &nbsp;/&nbsp; Name</div>

<div class="abs card" style="left:266px;top:510px"><div class="flag"></div><div class="thumb" role="img" aria-label="Red jacket" style="background:#d0452a"></div><div class="name">Etiam sit amet lectus quis</div><div class="price">$780.00</div></div>
<div class="abs card" style="left:432px;top:510px"><div class="flag"></div><div class="thumb" role="img" aria-label="Blue ski boot" style="background:#3fa3c4"></div><div class="name">Etiam sit amet lectus quis</div><div class="price">$780.00</div></div>
<div class="abs card" style="left:596px;top:510px"><div class="flag"></div><div class="thumb" role="img" aria-label="Avalanche beacon" style="background:#4d5b4e;width:22px;left:65px"></div><div class="name">Etiam sit amet lectus quis</div><div class="price">$780.00</div></div>
<div class="abs card" style="left:266px;top:682px"><div class="flag"></div><div class="thumb" role="img" aria-label="Orange harness" style="background:#d68a2a"></div><div class="name">Etiam sit amet lectus quis</div><div class="price">$780.00</div></div>
<div class="abs card" style="left:432px;top:682px"><div class="flag"></div><div class="thumb" role="img" aria-label="Blue ski boot" style="background:#4bb0cc"></div><div class="name">Etiam sit amet lectus quis</div><div class="price">$780.00</div></div>
<div class="abs card" style="left:596px;top:682px"><div class="flag"></div><div class="thumb" role="img" aria-label="Pair of skis" style="background:linear-gradient(90deg,#b03a2e,#2d6d4a,#c0752b)"></div><div class="name">Etiam sit amet lectus quis</div><div class="price">$780.00</div></div>

<div class="abs pager"><span>«</span><span>1</span><span class="on">2</span><span>3</span><span>4</span><span>5</span><span>6</span><span>7</span><span>8</span><span>9</span><span>10</span><span>»</span></div>

<section>
  <div class="abs testimonials"></div>
  <div class="abs t-label">Testimonials</div>
  <p class="abs t-text">Lorem ipsum dolor sit amet, consectetur adipiscing elit. Praesent libero lectus, tempus sed aliquam non, pellentesque et eros. Donec luctus nisl in nibh ultricies quis convallis justo convallis. T.B Lumby, BC</p>
  <div class="abs t-arrow"><svg width="30" height="30" viewBox="0 0 30 30"><path d="M7 15h15M16 9l6 6-6 6" stroke="#fff" stroke-width="2.4" fill="none"/></svg></div>
</section>

<footer>
  <div class="abs footer"></div>
  <div class="abs f-col" style="left:89px"><h3>Borealis Peak Stores</h3><ul><li>Abbotsford</li><li>Canmore</li><li>Courtenay</li><li>Medicine Hat</li><li>Nanaimo</li><li>Nelson</li><li>New Denver</li></ul></div>
  <div class="abs f-col" style="left:290px"><h3>Quick Links</h3><ul><li>Resucue Gear</li><li>Footwear</li><li>Clothing</li><li>Tents, Mats, Sleeping Bags</li><li>Camping Gear</li><li>Snow Sports</li><li>Brands</li></ul></div>
  <div class="abs f-col" style="left:457px"><h3>Products For</h3><ul><li>Search &amp; Rescue</li><li>Coast Guard</li><li>NVDK</li><li>Fire</li><li>Military</li><li>Law Enforcement</li></ul></div>
  <div class="abs f-col" style="left:612px"><h3>Newsletter</h3><p>Don't miss anynews. Subscribe to our Newsletter!</p><div class="f-input">Name</div><div class="f-input" style="margin-top:12px">Mail</div><div class="f-btn">Subscribe</div></div>
  <div class="abs base"></div>
  <div class="abs copyright">© 2014 Borealis Peak Outfitters Inc. All rights reserved.</div>
  <div class="abs social" style="left:616px"></div>
  <div class="abs social" style="left:650px"></div>
  <div class="abs social" style="left:684px"></div>
  <div class="abs social" style="left:719px"></div>
</footer>

<div class="abs veil"></div>
<div class="abs modal" role="dialog" aria-label="Registration required">
  <p class="modal-copy">Please register to enter and enjoy<br>Canada’s best selection of otdoorgear at special<br>pricing and termsthat reflect your<br>commitment tservice and duty, you unique<br>position and credentials</p>
  <div class="modal-btn">REGISTER</div>
</div>
<div class="abs close">X</div>
</body>
</html>
```